Design some Business Cards for Tavro

Thanks to everyone for their efforts. I will just be reviewing the first two entries from each contestant, so I'd suggest withdrawing entries which are not your favorites & going with your best two. Many thanks, Dorian

I was after a double sided business card for tavro.com.au. Tavro is a billing app and website for tradesman and service providers who move from site to site.

Firstly design for Dorian Webb with mobile 0487 555 904 & email demo@tavro.com.au.

Logo is attached, so please work with those colours. I've also included our url if you believe that is worth building in.

I would like the original working files and the business card will need to be produced for 3 different employees when the winner is selected.

Additional TAVRO text files if this helps.

```html
<!DOCTYPE html>
<html lang="en">
<head>
<meta charset="utf-8">
<title>Tavro Business Cards</title>
<link rel="stylesheet" href="https://fonts.googleapis.com/css2?family=Source+Sans+3:wght@400;600;700&display=swap">
<style>
  :root {
    --backdrop: #3a3a3c;
    --card: #ffffff;
    --brand-blue: #1f9bc7;
    --brand-red: #d9342b;
    --ink: #3f3f44;
    --rule: #e0533f;
  }
  * { box-sizing: border-box; margin: 0; padding: 0; }
  html, body {
    width: 1200px;
    height: 851px;
    overflow: hidden;
  }
  body {
    background: var(--backdrop);
    font-family: "Source Sans 3", sans-serif;
    position: relative;
  }
  .card {
    position: absolute;
    top: 280px;
    width: 500px;
    height: 290px;
    background: var(--card);
    border-radius: 24px;
    overflow: hidden;
  }
  .card--front { left: 60px; }
  .card--back { left: 640px; }

  .brand {
    position: absolute;
    display: flex;
    align-items: center;
    gap: 14px;
  }
  .brand__dot {
    border-radius: 50%;
    background: var(--brand-blue);
    flex: none;
  }
  .brand__name {
    color: var(--brand-blue);
    font-weight: 600;
    letter-spacing: 2px;
    line-height: 1;
  }

  .card--front .brand { left: 70px; top: 96px; }
  .card--front .brand__dot { width: 62px; height: 62px; }
  .card--front .brand__name { font-size: 70px; }
  .front__url {
    position: absolute;
    left: 78px;
    top: 196px;
    color: var(--brand-blue);
    font-size: 15px;
    letter-spacing: 1.5px;
  }

  .card--back .brand { left: 40px; top: 36px; }
  .card--back .brand__dot { width: 44px; height: 44px; }
  .card--back .brand__name { font-size: 50px; }
  .back__rule {
    position: absolute;
    left: 40px;
    right: 30px;
    top: 112px;
    height: 2px;
    background: var(--rule);
  }
  .contact {
    position: absolute;
    left: 40px;
    top: 128px;
    list-style: none;
    color: var(--ink);
    font-size: 15px;
  }
  .contact li {
    display: flex;
    align-items: center;
    gap: 10px;
    height: 22px;
  }
  .contact svg { width: 12px; height: 12px; fill: var(--brand-blue); flex: none; }
  .person {
    position: absolute;
    right: 34px;
    top: 178px;
    text-align: right;
  }
  .person__name {
    color: var(--brand-blue);
    font-weight: 700;
    font-size: 24px;
    line-height: 1.1;
    padding-bottom: 4px;
    border-bottom: 2px solid var(--rule);
  }
  .person__role {
    color: var(--brand-red);
    font-size: 21px;
    margin-top: 2px;
  }
</style>
</head>
<body>
  <section class="card card--front" aria-label="Card front">
    <div class="brand">
      <span class="brand__dot"></span>
      <span class="brand__name">TAVRO</span>
    </div>
    <p class="front__url">WWW.TAVRO.COM.AU</p>
  </section>

  <section class="card card--back" aria-label="Card back">
    <div class="brand">
      <span class="brand__dot"></span>
      <span class="brand__name">TAVRO</span>
    </div>
    <div class="back__rule"></div>
    <ul class="contact">
      <li>
        <svg viewBox="0 0 12 12" aria-hidden="true"><path d="M2.5 0.5 4.6 2.6 3.5 4.2c.8 1.7 2.1 3 3.8 3.8l1.6-1.1 2.1 2.1-1.5 2.2C4.8 11 .9 7.2.3 2z"/></svg>
        <span>0487 555 904</span>
      </li>
      <li>
        <svg viewBox="0 0 12 12" aria-hidden="true"><path d="M0 2h12v8H0z"/></svg>
        <span>dorian@tavro.com.au</span>
      </li>
      <li>
        <svg viewBox="0 0 12 12" aria-hidden="true"><circle cx="6" cy="6" r="6"/></svg>
        <span>www.tavro.com.au</span>
      </li>
    </ul>
    <div class="person">
      <p class="person__name">Dorian Webb</p>
      <p class="person__role">Director</p>
    </div>
  </section>
</body>
</html>
```